Product labels for new supplements business targeting high performing creative people

I need a label design for different supplements like Whey, BCAA, Melatonin etc. that I could customize for each use case separately.

The brand is called moonquell.life, and it would be the first design of the labels. We haven't sold any products yet, but the target audience is people with growth mindset, people who want to be as efficient as possible and are constantly looking to improve their lifestyle. As part of that, they are also working out, but don't know much about supplements yet. Mostly people between 20-34.

I don't have a too specific idea of the expected design, though it should be light, warm, smart and minimalist, maybe have some patterns. It should looks smart and clean (and expensive). Orange and golden might be the additional colors for white. I have attached the templates of some products that I plan to sell and also the logo of the brand.

Here's what I have used for inspiration:
Brands that I like and are somewhat similar in concept: https://www.vantrel.com/ (!!specially the way they
bring "how the product helps them" in focus, not "what the product is" & https://www.plomi.care/ &
https://www.delvora.com/sport/ & https://en.kalobrine.fr/ &
https://48sketchworks.com/profiles/marenhollowaydesign/designs/617482

Here's how different products look like: https://grenvolt.com/catalog

Target Market(s)

target audience is people with growth mindset, people who want to be as efficient as possible and are constantly looking to improve their lifestyle. As part of that, they are also working out, but don't know much about supplements yet. Mostly people between 20-34.

Industry/Entity Type

Supplements

Font styles to use
Sans Serif

Colors
FFC000
F8CF3A
FAE287
FDF2CF
FEFAEE
F0912C
F2A743
F7CA91
FBE8D2
FDF5EE
EE7325
F08F49
F5BC92
FAE3D3
FDF4ED

Requirements
Must have
• Clean, smart and minimalist design that can be applied for different products in different sizes, like Whey protein, BCAA, vitamins etc. available here: https://grenvolt.com/catalog
Nice to have
• Patterns, expensive look
Should not have
• Doodles, too many colors

```html
<!DOCTYPE html>
<html lang="en">
<head>
<meta charset="UTF-8">
<title>moonquell.life — BCAA 2:1:1 Wild Berry label</title>
<link rel="stylesheet" href="https://fonts.googleapis.com/css2?family=DM+Sans:wght@400;500&family=Montserrat:wght@600;800&display=swap">
<style>
  :root {
    --canvas: #f6f7f9;
    --label-dark: #0c0908;
    --label-brown: #33241f;
    --label-mid: #1c1412;
    --ink-light: #f4f1ee;
    --orange: #ee7325;
    --orange-deep: #e04a22;
    --orange-warm: #f0912c;
  }
  * { margin: 0; padding: 0; box-sizing: border-box; }
  html, body {
    width: 1200px;
    height: 1000px;
    overflow: hidden;
    background: var(--canvas);
  }
  .canvas {
    position: relative;
    width: 1200px;
    height: 1000px;
  }
  .label {
    position: absolute;
    left: 220px;
    top: 67px;
    width: 760px;
    height: 866px;
    overflow: hidden;
    color: var(--ink-light);
    background:
      linear-gradient(200deg, var(--label-brown) 0%, var(--label-dark) 45%, var(--label-mid) 75%, var(--label-brown) 100%);
  }
  .brand {
    position: absolute;
    top: 92px;
    left: 0;
    width: 100%;
    display: flex;
    flex-direction: column;
    align-items: center;
    gap: 26px;
  }
  .brand-dot {
    width: 22px;
    height: 22px;
    border-radius: 50%;
    background: var(--orange);
  }
  .brand-name {
    font-family: "DM Sans", sans-serif;
    font-weight: 500;
    font-size: 46px;
    letter-spacing: 0.5px;
    color: var(--ink-light);
  }
  .product-title {
    position: absolute;
    right: 142px;
    top: 318px;
    text-align: right;
    font-family: "Montserrat", sans-serif;
  }
  .product-name {
    font-weight: 800;
    font-size: 88px;
    line-height: 1;
    letter-spacing: 1px;
  }
  .product-flavour {
    margin-top: 26px;
    font-weight: 600;
    font-size: 48px;
    line-height: 1;
    letter-spacing: 2px;
  }
  .accent {
    position: absolute;
    left: 0;
    top: 0;
  }
  .benefits {
    position: absolute;
    left: 387px;
    top: 622px;
    font-family: "DM Sans", sans-serif;
    font-weight: 400;
    font-size: 23px;
    line-height: 31px;
    letter-spacing: 1px;
  }
  .label-footer {
    position: absolute;
    top: 806px;
    left: 106px;
    display: flex;
    gap: 38px;
    font-family: "DM Sans", sans-serif;
    font-weight: 400;
    font-size: 22px;
    letter-spacing: 1px;
  }
</style>
</head>
<body>
<main class="canvas">
  <section class="label">
    <div class="brand">
      <span class="brand-dot"></span>
      <span class="brand-name">moonquell.life</span>
    </div>

    <div class="product-title">
      <h1 class="product-name">BCAA 2:1:1</h1>
      <p class="product-flavour">WILD BERRY</p>
    </div>

    <svg class="accent" width="760" height="866" viewBox="0 0 760 866" aria-hidden="true">
      <defs>
        <linearGradient id="accent-fill" x1="0" y1="0" x2="1" y2="0">
          <stop offset="0" stop-color="var(--orange-warm)"/>
          <stop offset="1" stop-color="var(--orange-deep)"/>
        </linearGradient>
      </defs>
      <polygon points="278,542 656,530 329,581 345,772" fill="url(#accent-fill)"/>
    </svg>

    <p class="benefits">
      Essential branched<br>
      chain amino acids BCAA<br>
      Increases mucle growth,<br>
      reduces fatigue*
    </p>

    <footer class="label-footer">
      <span>DIETARY SUPPLEMENT</span>
      <span>Net Wt. 300g (10.58oz)</span>
    </footer>
  </section>
</main>
</body>
</html>
```